Dental office stationary (letterhead, envelopes), business cards, presentation folders

Nothing too dental outside of the logo. I will need all stationary, presentation folders, business cards. Would prefer to stay in the colors of the logo

Gordon Patel, DDS
Bright Haven Dental Implant Center
555-318-2790
info@brighthavendental.example
4817 NW Maple Crest Rd Unit B
Stuart, FL 00000

Also need appointment date and time
And cancellation policy
I want it to say “kindly ask for
A 48hr cancellation policy to avoid incurring a cancellation fee”

Industry/Entity Type

Dental

Colors
0054AA
0677BA
7BADD7
CADEEF
E8F1F8

Requirements
Must have
• Name of your office, name of doctor, address, phone number
Should not have
• Too much tooth/dental. Only the tooth in logo

```html
<!DOCTYPE html>
<html lang="en">
<head>
<meta charset="utf-8">
<title>Bright Haven Dental Implant Center — Stationery Set</title>
<link rel="stylesheet" href="https://fonts.googleapis.com/css2?family=Roboto:wght@400;500;700&display=swap">
<style>
  :root{
    --bg:#c9c9c9;
    --cyan:#17c1ef;
    --blue:#0d68b8;
    --teal:#1bbc9b;
    --ink:#333;
    --muted:#555;
    --paper:#fff;
    --shadow:2px 3px 5px rgba(0,0,0,.28);
    --brand-grad:linear-gradient(90deg,var(--cyan),var(--blue));
  }
  *{box-sizing:border-box;margin:0;padding:0}
  html,body{width:1200px;height:1011px;overflow:hidden}
  body{background:var(--bg);font-family:"Roboto",Arial,sans-serif;color:var(--ink);position:relative}
  .piece{position:absolute;background:var(--paper);box-shadow:var(--shadow);overflow:hidden}
  .brand-name{font-family:"Roboto",Arial,sans-serif;font-weight:400;letter-spacing:.04em;text-transform:uppercase;white-space:nowrap;display:flex;align-items:center;gap:.3em}
  .brand-name .dot{display:inline-block;width:.45em;height:.45em;border-radius:50%;background:currentColor}
  .arch-header{position:absolute;left:0;top:0;width:100%}
  .arch-header svg{display:block;width:100%;height:100%}
  .centered{position:absolute;left:0;right:0;display:flex;justify-content:center}

  /* business card */
  .business-card{left:53px;top:99px;width:325px;height:185px}
  .business-card svg{position:absolute;inset:0}
  .business-card .details{position:absolute;left:16px;top:36px;color:#fff}
  .business-card .doctor{font-weight:700;font-size:10.5px}
  .business-card .practice{font-size:8px;margin-top:2px}
  .business-card .address{font-size:8px;line-height:11px;margin-top:19px}
  .business-card .contact{font-size:8px;line-height:10.5px;margin-top:18px}
  .business-card .brand-name{position:absolute;left:168px;top:88px;font-size:17px;color:var(--cyan)}

  /* appointment card */
  .appointment-card{left:53px;top:315px;width:325px;height:185px}
  .appointment-card .band{position:absolute;left:0;top:0;width:100%;height:66px;background:var(--brand-grad)}
  .appointment-card .band .brand-name{font-size:20px;color:#fff;position:absolute;top:24px;left:0;right:0;justify-content:center}
  .appointment-card .rule{position:absolute;left:0;top:69px;width:100%;height:3px;background:var(--teal)}
  .appointment-card .tab{position:absolute;left:83px;top:70px;width:158px;height:13px;background:var(--teal);clip-path:polygon(0 0,100% 0,92% 100%,8% 100%);color:#fff;font-size:11.5px;text-align:center;line-height:13px}
  .appointment-card .dashed{position:absolute;left:21px;right:21px;top:109px;border-top:1px dashed #aaa}
  .appointment-card .fields{position:absolute;left:21px;right:21px;top:124px;display:flex;font-size:9.5px;color:var(--muted);align-items:flex-end}
  .appointment-card .fields .line{flex:1;border-bottom:1px solid #888;margin:0 3px 2px 2px;height:1px}
  .appointment-card .policy{position:absolute;left:0;right:0;top:150px;text-align:center;font-size:8.6px;line-height:11px;color:var(--muted)}
  .appointment-card .policy b{font-weight:700;color:#444}

  /* letterhead */
  .letterhead{left:402px;top:97px;width:285px;height:403px}
  .letterhead .arch-header{height:58px}
  .letterhead .brand-name,.folder-letter .brand-name{font-size:11px;color:var(--cyan)}
  .letter-body{position:absolute;left:26px;right:26px;font-family:Arial,sans-serif;color:#444}
  .letter-body .salutation{font-weight:700;font-size:6.5px;margin-bottom:10px}
  .letter-body p{font-size:4.3px;line-height:5.9px;margin-bottom:5.5px}
  .letter-body .closing{font-size:3.8px;font-weight:700;margin-top:9px}
  .signature{display:block;width:36px;height:12px;margin-top:8px;background:linear-gradient(90deg,#d8d8d8,#eee);border-radius:2px}
  .letter-footer{position:absolute;left:0;right:0;text-align:center;font-size:5px;color:#444}
  .letter-footer .addr{padding-bottom:3px}
  .letter-footer .contacts{display:inline-block;border-top:1px solid #999;padding:4px 0 0;margin:0 auto;white-space:nowrap}
  .letter-footer .contacts span{margin:0 3px}
  .letter-footer .ico{color:var(--teal)}
  .letter-footer .web em{font-style:normal;color:var(--teal)}

  /* envelope front */
  .envelope-front{left:715px;top:99px;width:430px;height:187px}
  .envelope-front .arch-header{height:90px}
  .envelope-front .brand-name{font-size:19px;color:var(--cyan)}
  .envelope-front .return{position:absolute;left:0;right:0;top:167px;text-align:center;font-size:7px;color:#444}

  /* envelope back */
  .envelope-back{left:713px;top:312px;width:434px;height:188px}
  .envelope-back .flap{position:absolute;left:0;top:0;width:100%;height:53px}
  .envelope-back .brand-name{font-size:15px;color:#fff}

  /* folder outside */
  .folder-outside{left:56px;top:540px;width:527px;height:372px}
  .folder-outside .back-cover{position:absolute;left:0;top:0;width:263px;height:100%;background:linear-gradient(100deg,var(--cyan),var(--blue))}
  .folder-outside .back-cover .brand-name{position:absolute;left:0;right:0;top:172px;justify-content:center;font-size:28px;color:#fff}
  .folder-outside .front-cover{position:absolute;left:263px;top:0;width:264px;height:100%;background:linear-gradient(100deg,#e6e7e9,#fbfbfb)}
  .folder-outside .front-cover .arch-header{height:54px}
  .folder-outside .front-cover .brand-name{font-size:10.5px;color:var(--cyan)}

  /* folder inside */
  .folder-inside{left:625px;top:538px;width:523px;height:376px;background:#fff}
  .folder-inside .left-panel{position:absolute;left:0;top:0;width:262px;height:100%;background:linear-gradient(90deg,#fff,#e9eaec)}
  .folder-inside .right-panel{position:absolute;left:262px;top:0;width:261px;height:100%;background:linear-gradient(90deg,#c4c6ca,#fff 60%)}
  .folder-letter{position:absolute;left:276px;top:17px;width:233px;height:240px;background:#fafafa}
  .folder-letter .arch-header{height:47px}
  .folder-letter .letter-body{left:21px;right:21px;top:102px}
  .folder-letter .letter-body .salutation{font-size:5.4px;margin-bottom:7px}
  .folder-letter .letter-body p{font-size:3.6px;line-height:4.8px;margin-bottom:4px}
  .folder-letter .letter-body .closing{font-size:3.2px;margin-top:5px}
  .folder-inside .pockets{position:absolute;left:0;top:0;width:100%;height:100%}
</style>
</head>
<body>

<svg width="0" height="0" style="position:absolute" aria-hidden="true">
  <defs>
    <linearGradient id="brandGradient" x1="0" y1="0" x2="1" y2="0">
      <stop offset="0" stop-color="#17c1ef"/>
      <stop offset="1" stop-color="#0d68b8"/>
    </linearGradient>
    <linearGradient id="pocketGradient" x1="0" y1="0" x2="1" y2="1">
      <stop offset="0" stop-color="#17c1ef"/>
      <stop offset="1" stop-color="#0d68b8"/>
    </linearGradient>
  </defs>
</svg>

<!-- Business card -->
<section class="piece business-card" aria-label="Business card">
  <svg viewBox="0 0 325 185" width="325" height="185" aria-hidden="true">
    <path d="M0,0 H207 C142,42 142,143 207,185 H0 Z" fill="url(#brandGradient)"/>
    <path d="M211,0 C148,42 148,143 211,185" fill="none" stroke="#1bbc9b" stroke-width="2"/>
  </svg>
  <div class="details">
    <div class="doctor">Gordon Patel, DDS</div>
    <div class="practice">Bright Haven Dental Implant Center</div>
    <div class="address">4817 NW Maple Crest Rd Unit B<br>Cedar Bluff, OR 00000</div>
    <div class="contact">☎ 555-318-2790<br>✉ info@brighthavendental.example<br>◍ www.brighthavendental.example</div>
  </div>
  <div class="brand-name"><span class="dot"></span>Bright Haven</div>
</section>

<!-- Appointment card -->
<section class="piece appointment-card" aria-label="Appointment card">
  <div class="band"><div class="brand-name"><span class="dot"></span>Bright Haven</div></div>
  <div class="rule"></div>
  <div class="tab">APPOINTMENT</div>
  <div class="dashed"></div>
  <div class="fields"><span>DATE :</span><span class="line"></span><span>TIME :</span><span class="line"></span></div>
  <p class="policy">If you are unable to keep this appointment please notify us at least<br><b>48 hours</b> in advance to avoid a broken appointment charge</p>
</section>

<!-- Letterhead -->
<section class="piece letterhead" aria-label="Letterhead">
  <div class="arch-header">
    <svg viewBox="0 0 100 30" preserveAspectRatio="none" aria-hidden="true">
      <path d="M0,0 H100 V29 Q50,-8 0,29 Z" fill="url(#brandGradient)"/>
      <path d="M0,29 Q50,-8 100,29" fill="none" stroke="#1bbc9b" stroke-width="2" vector-effect="non-scaling-stroke"/>
    </svg>
  </div>
  <div class="centered" style="top:33px"><div class="brand-name"><span class="dot"></span>Bright Haven</div></div>
  <div class="letter-body" style="top:124px">
    <div class="salutation">Dear Mr. Alder,</div>
    <p>Thank you for choosing our practice for your implant care. We have reviewed your records and prepared a treatment plan that fits your goals, timeline and budget. Please read the enclosed notes before your next visit.</p>
    <p>Your first appointment includes a full exam, digital scans and a review of your options. Our team will walk you through each step so you know what to expect.</p>
    <p>Most patients return to normal routines within a few days. We will schedule follow up visits to check healing and make sure your new teeth feel natural, look bright and work well for many years.</p>
    <p>If you have any questions about cost, insurance or care at home, call our office and we will gladly help.</p>
    <div class="closing">Sincerely,</div>
    <span class="signature" role="img" aria-label="Handwritten signature"></span>
  </div>
  <footer class="letter-footer" style="top:374px">
    <div class="addr">4817 NW Maple Crest Rd Unit B, Cedar Bluff, OR 00000</div>
    <div class="contacts"><span><span class="ico">☎</span> 555-318-2790</span><span><span class="ico">✉</span> info@brighthavendental.example</span><span class="web"><span class="ico">◍</span> www.<em>brighthavendental</em>.example</span></div>
  </footer>
</section>

<!-- Envelope front -->
<section class="piece envelope-front" aria-label="Envelope front">
  <div class="arch-header">
    <svg viewBox="0 0 100 30" preserveAspectRatio="none" aria-hidden="true">
      <path d="M0,0 H100 V29 Q50,-12 0,29 Z" fill="url(#brandGradient)"/>
      <path d="M0,29 Q50,-12 100,29" fill="none" stroke="#1bbc9b" stroke-width="2.5" vector-effect="non-scaling-stroke"/>
    </svg>
  </div>
  <div class="centered" style="top:50px"><div class="brand-name"><span class="dot"></span>Bright Haven</div></div>
  <div class="return">4817 NW Maple Crest Rd Unit B, Cedar Bluff, OR 00000</div>
</section>

<!-- Envelope back -->
<section class="piece envelope-back" aria-label="Envelope back">
  <svg class="flap" viewBox="0 0 434 53" aria-hidden="true">
    <path d="M0,0 H434 L424,38 Q420,52 404,52 H30 Q14,52 10,38 Z" fill="url(#brandGradient)"/>
  </svg>
  <div class="centered" style="top:19px"><div class="brand-name"><span class="dot"></span>Bright Haven</div></div>
</section>

<!-- Folder outside -->
<section class="piece folder-outside" aria-label="Presentation folder, outside">
  <div class="back-cover"><div class="brand-name"><span class="dot"></span>Bright Haven</div></div>
  <div class="front-cover">
    <div class="arch-header">
      <svg viewBox="0 0 100 30" preserveAspectRatio="none" aria-hidden="true">
        <path d="M0,0 H100 V30 Q50,-10 0,30 Z" fill="url(#brandGradient)"/>
        <path d="M0,30 Q50,-10 100,30" fill="none" stroke="#1bbc9b" stroke-width="2" vector-effect="non-scaling-stroke"/>
      </svg>
    </div>
    <div class="centered" style="top:32px"><div class="brand-name"><span class="dot"></span>Bright Haven</div></div>
    <footer class="letter-footer" style="top:345px">
      <div class="addr">4817 NW Maple Crest Rd Unit B, Cedar Bluff, OR 00000</div>
      <div class="contacts"><span><span class="ico">☎</span> 555-318-2790</span><span><span class="ico">✉</span> info@brighthavendental.example</span><span class="web"><span class="ico">◍</span> www.<em>brighthavendental</em>.example</span></div>
    </footer>
  </div>
</section>

<!-- Folder inside -->
<section class="piece folder-inside" aria-label="Presentation folder, inside">
  <div class="left-panel"></div>
  <div class="right-panel"></div>
  <div class="folder-letter">
    <div class="arch-header">
      <svg viewBox="0 0 100 30" preserveAspectRatio="none" aria-hidden="true">
        <path d="M0,0 H100 V30 Q50,-10 0,30 Z" fill="url(#brandGradient)"/>
        <path d="M0,30 Q50,-10 100,30" fill="none" stroke="#1bbc9b" stroke-width="2" vector-effect="non-scaling-stroke"/>
      </svg>
    </div>
    <div class="centered" style="top:27px"><div class="brand-name"><span class="dot"></span>Bright Haven</div></div>
    <div class="letter-body">
      <div class="salutation">Dear Mr. Alder,</div>
      <p>Thank you for choosing our practice for your implant care. We have reviewed your records and prepared a treatment plan that fits your goals, timeline and budget. Please read the enclosed notes before your next visit.</p>
      <p>Your first appointment includes a full exam, digital scans and a review of your options. Our team will walk you through each step so you know what to expect.</p>
      <p>Most patients return to normal routines within a few days. We will schedule follow up visits to check healing and make sure your new teeth feel natural, look bright and work well for many years.</p>
      <p>If you have any questions about cost, insurance or care at home, call our office and we will gladly help.</p>
      <div class="closing">Sincerely,</div>
    </div>
  </div>
  <svg class="pockets" viewBox="0 0 523 376" aria-hidden="true">
    <path d="M0,241 H236 Q244,241 245,250 L262,376 H0 Z" fill="url(#pocketGradient)"/>
    <path d="M288,240 H523 V376 H262 L277,252 Q279,240 288,240 Z" fill="url(#pocketGradient)"/>
  </svg>
</section>

</body>
</html>
```